Stationary design for boutique production house

We need a stationary design for our production house, 'Lorno Productions' based in Singapore. We produce microfilms as well as podcasts, talkshows and events. Our logo is a stylized icon of our director, who is also the executive producer and host of our programs, Lorno. Our main company colors are Red, Black and white. We would like a clean, minimalist design incorporating our existing company logo that conveys a sense of urbanism and elegance.

Logo and font files are attached. f

Target Market(s)

We focus on lifestyle media rather than entertainment.

Industry/Entity Type

Boutique

Font styles to use
Serif
Sans Serif

Colors
ec1f27
ffffff
000000

Requirements
Must have
• Our company logo and at least one of our company colors.
Nice to have
• Our address and contact information.
Should not have
• Changes made to the company logo (using only certain parts of it is fine though)

```html
<!DOCTYPE html>
<html lang="en">
<head>
<meta charset="utf-8">
<title>Lorno Productions — Stationery</title>
<link rel="stylesheet" href="https://fonts.googleapis.com/css2?family=Libre+Baskerville:wght@400;700&family=Arimo:wght@400&display=swap">
<style>
  :root {
    --red: #ec1f27;
    --deep-red: #a5161c;
    --black: #111111;
    --charcoal: #262626;
    --white: #ffffff;
    --paper: #ececec;
    --backdrop: #e4dac4;
    --serif: "Libre Baskerville", Georgia, serif;
    --sans: "Arimo", Arial, sans-serif;
  }
  * { box-sizing: border-box; margin: 0; padding: 0; }
  html, body { width: 1200px; height: 1118px; overflow: hidden; }
  body { background: var(--backdrop); position: relative; font-family: var(--serif); }

  /* Brand name lockup */
  .wordmark { font-family: var(--serif); font-weight: 400; line-height: 1.05; text-transform: uppercase; letter-spacing: 0.02em; }
  .wordmark-row { display: flex; align-items: center; gap: 10px; }
  .dot { border-radius: 50%; flex: none; }

  /* Letterhead */
  .letterhead {
    position: absolute; left: 600px; top: 163px; width: 560px; height: 792px;
    background: linear-gradient(180deg, #f3f3f3 0%, #e6e6e6 100%);
  }
  .letterhead-band {
    height: 118px; background: linear-gradient(90deg, var(--black), var(--charcoal));
    border-bottom: 4px solid var(--red);
    display: flex; justify-content: space-between; align-items: center; padding: 0 60px 0 40px;
  }
  .letterhead-band .wordmark { color: var(--white); font-size: 17px; }
  .letterhead-band .dot { width: 12px; height: 12px; background: var(--red); }
  .letterhead-address { color: var(--white); font-size: 11px; line-height: 1.45; }
  .letterhead-address .phone { font-family: var(--sans); font-size: 10.5px; margin-top: 4px; display: block; }

  /* Envelope */
  .envelope {
    position: absolute; left: 40px; top: 163px; width: 520px; height: 270px;
    background: #e9e9e9; overflow: hidden;
  }
  .envelope-flap-line { position: absolute; left: 0; right: 0; top: 38px; height: 5px; background: var(--deep-red); }
  .envelope-mark { position: absolute; left: 40px; top: 92px; }
  .envelope-mark .wordmark { color: var(--black); font-size: 22px; }
  .envelope-mark .dot { width: 14px; height: 14px; background: var(--red); }
  .envelope-band {
    position: absolute; left: 0; right: 0; bottom: 0; height: 52px;
    background: var(--black); border-top: 4px solid var(--red);
    display: flex; align-items: center; padding-left: 40px;
    color: var(--white); font-size: 13px; letter-spacing: 0.02em;
  }

  /* Business card back */
  .card { position: absolute; width: 340px; height: 200px; }
  .card-back { left: 40px; top: 470px; display: flex; background: var(--black); }
  .card-back-brand {
    width: 138px; background: #ededed; border-right: 3px solid var(--red);
    display: flex; align-items: center; justify-content: center;
  }
  .card-back-brand .wordmark { color: var(--black); font-size: 12px; text-align: center; }
  .card-back-brand .wordmark-row { flex-direction: column; gap: 8px; }
  .card-back-brand .dot { width: 10px; height: 10px; background: var(--red); }
  .contact-list { list-style: none; padding: 46px 0 0 14px; color: var(--white); font-size: 8.5px; }
  .contact-list li { display: flex; gap: 8px; margin-bottom: 14px; line-height: 1.5; }
  .contact-list .phone-line { font-family: var(--sans); }
  .icon { width: 9px; height: 9px; flex: none; margin-top: 2px; }

  /* Business card front */
  .card-front {
    left: 40px; top: 705px; background: linear-gradient(160deg, #b3121a, var(--deep-red));
    display: flex; align-items: center; justify-content: center;
  }
  .card-front .wordmark { color: var(--white); font-size: 20px; }
  .card-front .dot { width: 13px; height: 13px; background: var(--black); }
</style>
</head>
<body>

  <section class="letterhead" aria-label="Letterhead">
    <header class="letterhead-band">
      <div class="wordmark-row">
        <span class="dot"></span>
        <span class="wordmark">Lorno Productions</span>
      </div>
      <address class="letterhead-address" style="font-style:normal">
        18 Kallang Way,<br>
        Harbourlight Building,<br>
        #03 12, Singapore 349211
        <span class="phone">+65 6390 4417</span>
      </address>
    </header>
  </section>

  <section class="envelope" aria-label="Envelope">
    <div class="envelope-flap-line"></div>
    <div class="envelope-mark wordmark-row">
      <span class="dot"></span>
      <span class="wordmark">Lorno<br>Productions</span>
    </div>
    <div class="envelope-band">18 Kallang Way, Harbourlight Building, #03 12, Singapore 349211</div>
  </section>

  <section class="card card-back" aria-label="Business card, back">
    <div class="card-back-brand">
      <div class="wordmark-row">
        <span class="dot"></span>
        <span class="wordmark">Lorno<br>Productions</span>
      </div>
    </div>
    <ul class="contact-list">
      <li class="phone-line">
        <svg class="icon" viewBox="0 0 10 10"><rect width="10" height="10" fill="#ec1f27"/><path d="M3 2.2 L4.2 3.6 L3.6 4.3 Q4.6 5.8 5.7 6.4 L6.4 5.8 L7.8 7 L7 7.9 Q4.2 7.4 2.1 3 Z" fill="#fff"/></svg>
        <span>+65 6390 4417</span>
      </li>
      <li>
        <svg class="icon" viewBox="0 0 10 10"><rect width="10" height="10" fill="#ec1f27"/><rect x="2" y="3" width="6" height="4" fill="none" stroke="#fff" stroke-width="0.8"/><path d="M2 3 L5 5.3 L8 3" fill="none" stroke="#fff" stroke-width="0.8"/></svg>
        <span>hello@lornoproductions.sg</span>
      </li>
      <li>
        <svg class="icon" viewBox="0 0 10 10"><rect width="10" height="10" fill="#ec1f27"/><path d="M5 8.2 L3 5 A2.3 2.3 0 1 1 7 5 Z" fill="#fff"/><circle cx="5" cy="4" r="0.8" fill="#ec1f27"/></svg>
        <span>18 Kallang Way, Harbourlight<br>Building, #03-12, Singapore 349211</span>
      </li>
    </ul>
  </section>

  <section class="card card-front" aria-label="Business card, front">
    <div class="wordmark-row">
      <span class="dot"></span>
      <span class="wordmark">Lorno<br>Productions</span>
    </div>
  </section>

</body>
</html>
```